Design a building access mobile app for Quillo by Tamberlin Entry Systems

Hello, We're looking for an awesome designer to create an app design for our app Quillo, by Tamberlin Entry Systems. the mobile app allows employees open their office doors with their mobile phone. this means they don't have to use those plastic card badges or keys. We like clean modern design, dark and light themes. We don't have a logo yet.
Updates

Reason: Waiting on a couple designers to submit concepts

Target Market(s)

Commercial and employees

Industry/Entity Type

Building

Font styles to use
Sans Serif
Other font styles liked:
• Oswald extra light

Requirements
Must have
• nice clean design

```html
<!DOCTYPE html>
<html lang="en">
<head>
<meta charset="utf-8">
<title>Quillo – Door Access</title>
<link href="https://fonts.googleapis.com/css2?family=Montserrat:wght@400;500;600&display=swap" rel="stylesheet">
<style>
  :root {
    --screen-bg: #0b0b0c;
    --bar-bg: #0e0e0f;
    --divider: #2a2b2d;
    --accent: #1a9cf0;
    --accent-deep: #1686c9;
    --accent-dim: #0f4f7a;
    --ring-inner: #1b2a36;
    --text-light: #ffffff;
  }
  * { margin: 0; padding: 0; box-sizing: border-box; }
  html, body {
    width: 800px; height: 1200px; overflow: hidden;
    background: var(--screen-bg);
    font-family: "Montserrat", sans-serif;
  }
  .app-screen {
    position: relative; width: 800px; height: 1200px;
    background:
      radial-gradient(circle at 50% 54%, rgba(26,156,240,0.10) 0, rgba(26,156,240,0) 340px),
      var(--screen-bg);
  }
  .top-bar {
    height: 136px; display: flex; align-items: center; justify-content: center;
    position: relative; background: var(--bar-bg);
    border-bottom: 1px solid var(--divider);
  }
  .menu-button { position: absolute; left: 31px; top: 70px; width: 46px; }
  .menu-button span { display: block; height: 2px; background: var(--text-light); margin-bottom: 14px; }
  .menu-button span:nth-child(2) { width: 44px; margin-left: 2px; }
  .brand-name {
    color: var(--text-light); font-weight: 600; font-size: 34px; letter-spacing: 1px;
    margin-top: 16px;
  }
  .location-bar {
    height: 124px; display: flex; align-items: center; justify-content: space-between;
    padding: 0 30px; border-bottom: 1px solid var(--divider);
  }
  .location-name {
    color: var(--accent); font-weight: 500; font-size: 40px; letter-spacing: 1px;
  }
  .door-control {
    position: absolute; left: 50%; top: 410px; transform: translateX(-50%);
    width: 520px; height: 520px;
  }
  .door-label {
    position: absolute; inset: 0; display: flex; align-items: center; justify-content: center;
    color: var(--text-light); font-weight: 500; font-size: 62px; letter-spacing: 2px;
  }
</style>
</head>
<body>
<main class="app-screen">
  <header class="top-bar">
    <div class="menu-button" aria-label="Menu"><span></span><span></span><span></span></div>
    <div class="brand-name">Quillo</div>
  </header>

  <nav class="location-bar">
    <svg width="26" height="40" viewBox="0 0 26 40" aria-label="Previous location">
      <polyline points="22,3 5,20 22,37" fill="none" stroke="var(--accent)" stroke-width="3"/>
    </svg>
    <h1 class="location-name">OFFICE LOCATION</h1>
    <svg width="26" height="40" viewBox="0 0 26 40" aria-label="Next location">
      <polyline points="4,3 21,20 4,37" fill="none" stroke="var(--accent)" stroke-width="3"/>
    </svg>
  </nav>

  <section class="door-control" aria-label="Open door">
    <svg width="520" height="520" viewBox="0 0 520 520">
      <defs>
        <filter id="ring-glow" x="-20%" y="-20%" width="140%" height="140%">
          <feGaussianBlur stdDeviation="9" result="blur"/>
          <feMerge><feMergeNode in="blur"/><feMergeNode in="SourceGraphic"/></feMerge>
        </filter>
      </defs>
      <circle cx="260" cy="260" r="238" fill="#0e0f10" stroke="var(--accent)" stroke-width="2.5" filter="url(#ring-glow)"/>
      <circle cx="260" cy="260" r="208" fill="none" stroke="var(--ring-inner)" stroke-width="4"/>
      <polygon points="58,227 26,260 58,293" fill="var(--accent-dim)"/>
      <polygon points="91,222 52,260 91,298" fill="var(--accent-deep)"/>
      <polygon points="462,227 494,260 462,293" fill="var(--accent-dim)"/>
      <polygon points="429,222 468,260 429,298" fill="var(--accent-deep)"/>
    </svg>
    <div class="door-label">DOOR</div>
  </section>
</main>
</body>
</html>
```